Fitness Equipment Repair Business Needs a Catchy New Business Card

We have an existing business card, however, it is quite plain and boring. We are expanding primarily in the commercial area (gyms, studios, apartment complexes etc). The business card will serve as eye candy to those managers/owners that can't be met for a face to face.
Originally I was planning for a brochure as well, but all of our information is better summarized on our website. (brightloopservice.ca).
I would like the card to match the colour scheme of the website and utilize the logo. It should have a professional clean feel to it, however, a little colouring outside the lines wouldn't hurt.
The example card is for my service technician (Colin Marsh). If possible I would like to be able to edit the text to use for more than one person.

Industry/Entity Type

Appliance Repair

Contact Information for Business Card

Clean, crisp and professional but needs to be eye catching. Preferably using the black, white and red colour scheme matching the website. Double sided would be nice, but is not necessary.

Colors
ec1f27
ffffff
000000

Requirements
Must have
• Must be able to edit name, phone number and title to use for multiple people. Must show the company website (brightloopservice.ca).

```html
<!DOCTYPE html>
<html lang="en">
<head>
<meta charset="utf-8">
<title>Brightloop Service – Business Card</title>
<link rel="stylesheet" href="https://fonts.googleapis.com/css2?family=Marcellus+SC&family=PT+Sans:wght@400;700&display=swap">
<style>
  :root {
    --red: #ec1f27;
    --black: #000000;
    --white: #ffffff;
    --stage: #e7e4df;
    --muted: #d9d9d9;
  }
  * { box-sizing: border-box; margin: 0; padding: 0; }
  html, body { width: 1200px; height: 987px; overflow: hidden; }
  body { background: var(--stage); position: relative; font-family: "PT Sans", sans-serif; }

  .card { position: absolute; left: 293px; width: 615px; height: 351px; overflow: hidden; }

  /* Front */
  .card-front { top: 130px; background: var(--black); color: var(--white); }
  .brand {
    position: absolute; left: 128px; top: 66px;
    display: flex; align-items: center; gap: 14px;
  }
  .brand-dot { width: 82px; height: 82px; border-radius: 50%; background: var(--red); flex: none; }
  .brand-name {
    font-family: "Marcellus SC", serif; font-size: 22px; color: var(--white);
    letter-spacing: 0.5px;
  }
  .person { position: absolute; right: 340px; top: 206px; text-align: right; }
  .person-name {
    font-family: "Marcellus SC", serif; font-size: 21px; color: var(--red);
    font-weight: 400; letter-spacing: 1px; line-height: 28px;
  }
  .person-title {
    font-family: "Marcellus SC", serif; font-size: 15px; color: var(--muted);
    letter-spacing: 1px; line-height: 24px;
  }
  .person-address { font-size: 15px; line-height: 24px; margin-top: 4px; color: var(--white); }
  .contact { position: absolute; left: 308px; top: 210px; list-style: none; }
  .contact li {
    display: flex; align-items: center; gap: 8px;
    font-size: 15px; line-height: 24px; color: var(--white);
  }
  .contact svg { width: 13px; height: 13px; fill: var(--red); flex: none; }
  .front-rule {
    position: absolute; left: 0; right: 0; bottom: 0; height: 12px;
    background: var(--red); border-top: 5px solid var(--white);
  }

  /* Back */
  .card-back { top: 506px; background: var(--red); color: var(--white); }
  .back-mark { position: absolute; left: 22px; top: 24px; width: 220px; }
  .back-mark-dot {
    display: block; width: 180px; height: 180px; border-radius: 50%;
    background: var(--white); margin-left: 14px;
  }
  .back-mark-name {
    font-family: "Marcellus SC", serif; font-size: 32px; line-height: 36px;
    color: var(--white); margin-top: 26px; letter-spacing: 0.5px;
  }
  .back-brand { position: absolute; left: 293px; top: 266px; }
  .back-name { font-family: "Marcellus SC", serif; font-size: 25px; letter-spacing: 0.5px; line-height: 30px; }
  .back-url { font-size: 15px; letter-spacing: 3px; line-height: 22px; }
</style>
</head>
<body>

<section class="card card-front" aria-label="Business card front">
  <div class="brand">
    <span class="brand-dot"></span>
    <span class="brand-name">Brightloop Service</span>
  </div>

  <div class="person">
    <p class="person-name">Colin Marsh</p>
    <p class="person-title">Service technician</p>
    <p class="person-address">1875 Larkfield Road NW<br>Edmonton AB T5K 0Z1</p>
  </div>

  <ul class="contact">
    <li>
      <svg viewBox="0 0 24 24" aria-hidden="true"><path d="M6.6 10.8a15.1 15.1 0 0 0 6.6 6.6l2.2-2.2c.3-.3.7-.4 1-.2 1.1.4 2.3.6 3.6.6.6 0 1 .4 1 1V20c0 .6-.4 1-1 1A17 17 0 0 1 3 4c0-.6.4-1 1-1h3.5c.6 0 1 .4 1 1 0 1.3.2 2.5.6 3.6.1.3 0 .7-.2 1z"/></svg>
      555-310-2284(Personal)
    </li>
    <li>
      <svg viewBox="0 0 24 24" aria-hidden="true"><path d="M6.6 10.8a15.1 15.1 0 0 0 6.6 6.6l2.2-2.2c.3-.3.7-.4 1-.2 1.1.4 2.3.6 3.6.6.6 0 1 .4 1 1V20c0 .6-.4 1-1 1A17 17 0 0 1 3 4c0-.6.4-1 1-1h3.5c.6 0 1 .4 1 1 0 1.3.2 2.5.6 3.6.1.3 0 .7-.2 1z"/></svg>
      555-410-7731(Service Line)
    </li>
    <li>
      <svg viewBox="0 0 24 24" aria-hidden="true"><path d="M2 5h20v14H2zM3.5 6.5 12 13l8.5-6.5z" fill-rule="evenodd"/></svg>
      hello@brightloopservice.ca
    </li>
    <li>
      <svg viewBox="0 0 24 24" aria-hidden="true"><circle cx="12" cy="12" r="10"/><path d="M2 12h20M12 2c3 3 3 17 0 20M12 2c-3 3-3 17 0 20" stroke="#000" stroke-width="1.5" fill="none"/></svg>
      www.brightloopservice.ca
    </li>
  </ul>

  <div class="front-rule"></div>
</section>

<section class="card card-back" aria-label="Business card back">
  <div class="back-mark">
    <span class="back-mark-dot"></span>
    <p class="back-mark-name">Brightloop<br>Service</p>
  </div>
  <div class="back-brand">
    <p class="back-name">Brightloop Service</p>
    <p class="back-url">www.brightloopservice.ca</p>
  </div>
</section>

</body>
</html>
```